Brightway Haus Inc. Business Card Design

Brightway Haus Inc. is in search of a great clean design for our business cards!

Looking to incorporate our full logo and watermark on side one (however, I am open to having the text and watermark separated within the design.)

On side two, I am looking to have contact information (Name, Position, Phone #, Email, Website (www.thebrightwayhaus.ca). Can have the logo and/or watermark as part of the design if applicable.

Please add tagline "Where Shine Counts" on either side 1 or 2. This tagline can be in a sans serif, serif or cursive font as long as it compliments overall design. Capitalization can be title or sentence case depending on how it fits within the design.

Get creative!! Looking for a clean, crisp, premium design! Looking for a glossy card finish with spot UV features when printed. Cards will also be printed with rounded corners. Standard dimensions (3.5 x 2).

Target Market(s)

B2B - primary clients are business owners or property management corporations. (residential jobs are few and far between)

Industry/Entity Type

Business

Contact Information for Business Card

- clean, crisp design
- double sided
- spot UV accents and glossy finish upon printing
- standard business card size (3.5 x 2) with rounded corners
- please see project description for requirements per side

Font styles to use
Sans Serif

Requirements
Must have
• - adequate bleeds with print ready files
• - cohesive design elements between side 1 & 2
• - spot UV elements (can be on both sides or just one, use your discretion)
• - colour pallet should match the logo file provided
• - incorporate tagline "where shine counts" (this tagline can be in a serif or sans serif font as long as it is complimentary to the overall design.
Nice to have
• - Premium elements with a clean design
Should not have
• - Please omit cartoon or whimsical like designs, think premium.
• - Colours should not stray from the pallet of the provided logo.

```html
<!DOCTYPE html>
<html lang="en">
<head>
<meta charset="utf-8">
<title>Brightway Haus Inc. Business Cards</title>
<link rel="stylesheet" href="https://fonts.googleapis.com/css2?family=Open+Sans:wght@400;600;700&display=swap">
<style>
  :root {
    --teal: #0fb8ba;
    --navy: #1b2350;
    --white: #ffffff;
    --silver: #cfd0d2;
    --backdrop: #c9c9c9;
  }
  html, body {
    margin: 0;
    padding: 0;
    width: 1200px;
    height: 960px;
    overflow: hidden;
    background: var(--backdrop);
    font-family: "Open Sans", sans-serif;
  }
  .canvas {
    position: relative;
    width: 1200px;
    height: 960px;
  }
  .card {
    position: absolute;
    width: 600px;
    height: 342px;
    border-radius: 20px;
    overflow: hidden;
    box-shadow: 0 4px 10px rgba(0,0,0,0.35);
  }
  .card-front { left: 314px; top: 113px; background: var(--teal); }
  .card-back  { left: 311px; top: 472px; background: var(--navy); }

  .front-curve { position: absolute; inset: 0; }

  .contact {
    position: absolute;
    left: 26px;
    top: 70px;
    color: var(--white);
    font-size: 14.5px;
    line-height: 18.5px;
  }
  .contact-name { font-weight: 700; font-size: 15.5px; margin: 0; }
  .contact-role { margin: 0 0 19px; }
  .contact-address { margin: 0 0 6px; }
  .contact-list { list-style: none; margin: 0; padding: 0; }
  .contact-list li { display: flex; align-items: center; height: 19px; }
  .contact-list svg { width: 12px; height: 12px; margin-right: 10px; fill: var(--white); }

  .brand-front {
    position: absolute;
    left: 300px;
    top: 156px;
    display: flex;
    align-items: center;
    gap: 7px;
    color: var(--navy);
    font-weight: 700;
    font-size: 22px;
    letter-spacing: 0.5px;
    white-space: nowrap;
  }
  .brand-mark { width: 16px; height: 16px; background: var(--teal); }

  .brand-back {
    position: absolute;
    left: 0;
    right: 0;
    top: 148px;
    text-align: center;
    color: var(--silver);
    font-weight: 700;
    font-size: 38px;
    letter-spacing: 1px;
  }
  .tagline {
    position: absolute;
    left: 100px;
    right: 100px;
    top: 276px;
    display: flex;
    align-items: center;
    color: var(--white);
    font-weight: 600;
    font-size: 17px;
    white-space: nowrap;
  }
  .tagline-rule { flex: 1; height: 1px; }
  .tagline-rule.left  { background: linear-gradient(to right, transparent, var(--white)); }
  .tagline-rule.right { background: linear-gradient(to left, transparent, var(--white)); }
  .tagline-text { padding: 0 2px; }
</style>
</head>
<body>
<main class="canvas">

  <section class="card card-front">
    <svg class="front-curve" viewBox="0 0 600 342" width="600" height="342">
      <ellipse cx="640" cy="171" rx="406" ry="182" fill="var(--white)"/>
      <ellipse cx="640" cy="171" rx="404" ry="180" fill="var(--navy)"/>
      <ellipse cx="652" cy="171" rx="400" ry="180" fill="var(--white)"/>
    </svg>

    <div class="contact">
      <p class="contact-name">MARA ELLISON</p>
      <p class="contact-role">CEO/FOUNDER</p>
      <p class="contact-address">412 Harbourview Road<br>Halifax, Nova Scotia B3H 2Y9</p>
      <ul class="contact-list">
        <li><svg viewBox="0 0 12 12"><path d="M1 4c0-2 2-3 5-3s5 1 5 3H8.5V3h-5v1zM2 5h8l1 6H1z"/></svg>902 555 0148</li>
        <li><svg viewBox="0 0 12 12"><path d="M3 0h6v12H3zM4 1.5v8h4v-8z"/></svg>902 555 0173</li>
        <li><svg viewBox="0 0 12 12"><path d="M3 1h6v3H3zM1 5h10v5H9V8H3v2H1zM3.5 9h5v2h-5z"/></svg>902 555 0190</li>
        <li><svg viewBox="0 0 12 12"><path d="M0 3h12v7H0zM1 4l5 3 5-3z" fill-rule="evenodd"/></svg>mara@brightwayhaus.ca</li>
        <li><svg viewBox="0 0 12 12"><circle cx="6" cy="6" r="5.5"/></svg>www.thebrightwayhaus.ca</li>
      </ul>
    </div>

    <div class="brand-front">
      <span class="brand-mark"></span>
      <span class="brand-name">BRIGHTWAY HAUS INC.</span>
    </div>
  </section>

  <section class="card card-back">
    <div class="brand-back">BRIGHTWAY HAUS INC.</div>
    <div class="tagline">
      <span class="tagline-rule left"></span>
      <span class="tagline-text">Where Shine Counts</span>
      <span class="tagline-rule right"></span>
    </div>
  </section>

</main>
</body>
</html>
```